Stonebridge Building and Projects business cards

A business card with watermark background (construction work)

Company logo attached

Home improvement projects
House renovations
Bathroom and kitchen renovations
House extensions
New builds and granny flats

Director Omar Haddani
(Phone number)
omar@sbpbuilding.com.au
(Instagram logo) sbp_building

```html
<!DOCTYPE html>
<html lang="en">
<head>
<meta charset="utf-8">
<title>Stonebridge Building and Projects – Business Cards</title>
<link rel="stylesheet" href="https://fonts.googleapis.com/css2?family=Roboto:wght@400;500;700&display=swap">
<style>
  :root {
    --bg: #2b2b2d;
    --card: #131315;
    --card-edge: #1c1c1f;
    --blue: #1e88d2;
    --white: #f2f2f2;
    --grey: #8c8c90;
    --dim: #4a4a4e;
  }
  * { box-sizing: border-box; margin: 0; padding: 0; }
  html, body { width: 1200px; height: 1050px; overflow: hidden; }
  body {
    background: var(--bg);
    font-family: "Roboto", Arial, sans-serif;
    color: var(--white);
    position: relative;
  }
  .card {
    position: absolute;
    left: 260px;
    width: 680px;
    height: 390px;
    background: var(--card);
    border-radius: 30px;
    overflow: hidden;
    box-shadow: 0 14px 40px rgba(0,0,0,.55);
    border: 1px solid var(--card-edge);
  }
  .card--front { top: 90px; }
  .card--back { top: 560px; }

  /* front */
  .brand {
    position: absolute;
    right: 60px;
    top: 58px;
    text-align: left;
    width: 300px;
  }
  .brand__name {
    font-size: 40px;
    font-weight: 700;
    color: var(--blue);
    line-height: 1;
    display: flex;
    align-items: center;
    gap: 10px;
  }
  .brand__mark {
    width: 14px; height: 14px;
    background: var(--blue);
    display: inline-block;
  }
  .brand__sub {
    font-size: 19px;
    font-weight: 500;
    color: var(--white);
    margin-top: 8px;
    padding-bottom: 8px;
    border-bottom: 2px solid var(--blue);
  }
  .brand__tagline {
    font-size: 19px;
    color: var(--blue);
    margin-top: 6px;
    display: inline-block;
    padding-bottom: 4px;
    border-bottom: 2px solid var(--blue);
  }
  .rule {
    position: absolute;
    left: 340px;
    top: 176px;
    width: 250px;
    height: 2px;
    background: var(--white);
  }
  .divider {
    position: absolute;
    left: 230px;
    top: 242px;
    width: 420px;
    height: 2px;
    background: linear-gradient(90deg, var(--blue), var(--blue) 55%, var(--white) 55%);
  }
  .edge-tab {
    position: absolute;
    left: -22px;
    top: 300px;
    width: 44px;
    height: 44px;
    border-radius: 50%;
    background: var(--blue);
  }
  .person {
    position: absolute;
    left: 44px;
    top: 222px;
  }
  .person__name { font-size: 24px; font-weight: 700; color: var(--blue); }
  .person__role { font-size: 16px; color: var(--white); margin-top: 4px; }
  .contacts {
    position: absolute;
    list-style: none;
    font-size: 16px;
  }
  .contacts li { display: flex; align-items: center; gap: 12px; margin-bottom: 10px; }
  .contacts svg { width: 16px; height: 16px; flex: none; }
  .contacts--left { left: 44px; top: 300px; }
  .contacts--right { left: 330px; top: 262px; }

  /* back */
  .wordmark {
    position: absolute;
    left: 0; right: 0;
    top: 60px;
    text-align: center;
    font-size: 84px;
    font-weight: 700;
    color: var(--grey);
    letter-spacing: 2px;
  }
  .services {
    position: absolute;
    left: 0; right: 0;
    top: 224px;
    height: 82px;
    background: var(--blue);
    display: flex;
    flex-direction: column;
    justify-content: center;
    align-items: center;
    font-size: 18px;
    line-height: 1.5;
    color: var(--white);
  }
  .services .sep { margin: 0 10px; }
  .socials {
    position: absolute;
    left: 0; right: 0;
    top: 330px;
    display: flex;
    justify-content: center;
    gap: 40px;
    font-size: 17px;
    list-style: none;
  }
  .socials li { display: flex; align-items: center; gap: 10px; }
  .socials svg { width: 16px; height: 16px; }
</style>
</head>
<body>

<section class="card card--front" aria-label="Business card front">
  <div class="brand">
    <div class="brand__name"><span class="brand__mark"></span>Stonebridge</div>
    <div class="brand__sub">Building and Projects</div>
    <div class="brand__tagline">As solid as stone!</div>
  </div>

  <div class="divider"></div>
  <div class="edge-tab"></div>

  <div class="person">
    <div class="person__name">Omar Haddani</div>
    <div class="person__role">Managing Director</div>
  </div>

  <ul class="contacts contacts--left">
    <li>
      <svg viewBox="0 0 16 16" aria-hidden="true"><circle cx="8" cy="8" r="7" fill="none" stroke="var(--blue)" stroke-width="1.5"/><path d="M5.5 4.5l1.5 1.5-1 1c.6 1.2 1.4 2 2.5 2.5l1-1 1.5 1.5-1 1c-2.5-.3-4.7-2.5-5-5z" fill="var(--blue)"/></svg>
      0412 384 907
    </li>
    <li>
      <svg viewBox="0 0 16 16" aria-hidden="true"><circle cx="8" cy="8" r="7" fill="var(--blue)"/></svg>
      sbp_building
    </li>
  </ul>

  <ul class="contacts contacts--right">
    <li>
      <svg viewBox="0 0 16 16" aria-hidden="true"><rect x="1.5" y="3.5" width="13" height="9" rx="1" fill="none" stroke="var(--blue)" stroke-width="1.5"/><path d="M1.5 4l6.5 5 6.5-5" fill="none" stroke="var(--blue)" stroke-width="1.5"/></svg>
      omar@sbpbuilding.com.au
    </li>
    <li>
      <svg viewBox="0 0 16 16" aria-hidden="true"><circle cx="8" cy="8" r="7" fill="var(--blue)"/><path d="M1 8h14M8 1c-3 3.5-3 10.5 0 14M8 1c3 3.5 3 10.5 0 14" fill="none" stroke="var(--card)" stroke-width="1"/></svg>
      www.sbpbuilding.com.au
    </li>
  </ul>
</section>

<section class="card card--back" aria-label="Business card back">
  <div class="wordmark">Stonebridge</div>

  <div class="services">
    <div>Home Improvement Projects<span class="sep">|</span>House Renovations<span class="sep">|</span>House Extensions</div>
    <div>Bathroom &amp; Kitchen Renovations<span class="sep">|</span>New Builds &amp; Granny Flats</div>
  </div>

  <ul class="socials">
    <li>
      <svg viewBox="0 0 16 16" aria-hidden="true"><circle cx="8" cy="8" r="7" fill="var(--blue)"/></svg>
      sbp_building
    </li>
    <li>
      <svg viewBox="0 0 16 16" aria-hidden="true"><circle cx="8" cy="8" r="7" fill="var(--blue)"/><path d="M1 8h14M8 1c-3 3.5-3 10.5 0 14M8 1c3 3.5 3 10.5 0 14" fill="none" stroke="var(--card)" stroke-width="1"/></svg>
      sbpbuilding.com.au
    </li>
  </ul>
</section>

</body>
</html>
```